Visit card

Industry/Entity Type

Health Care

Contact Information for Business Card

O VITALIS SYSTEMS
Odile Brevard - chef de Projet

Requirements
Must have
• 318 Gaston Lemaire Street 59710 BÉTHUNE Tel: 33 (0) 327 481 605 Mobile: 06 42 19 37 64 Web: www.quorvexsystems.example Contact: o.brevard@o-vitalissystems.example
Should not have
• Respect for color

```html
<!DOCTYPE html>
<html lang="fr">
<head>
<meta charset="utf-8">
<title>O Vitalis Systems – Business Card</title>
<link rel="stylesheet" href="https://fonts.googleapis.com/css2?family=Lato:wght@400;700;900&display=swap">
<style>
  :root {
    --stage: #2a2a2a;
    --card-dark: #3b3b3c;
    --card-dark-edge: #2e2e2f;
    --accent-red: #e31e2d;
    --paper-white: #ffffff;
    --text-light: #f2f2f2;
    --text-muted: #d6d6d6;
  }
  * { box-sizing: border-box; margin: 0; padding: 0; }
  html, body { width: 1200px; height: 896px; overflow: hidden; }
  body {
    background: var(--stage);
    font-family: "Lato", sans-serif;
    position: relative;
  }
  .card {
    position: absolute;
    left: 320px;
    width: 560px;
    height: 320px;
    border-radius: 22px;
    overflow: hidden;
    background: linear-gradient(135deg, var(--card-dark) 0%, var(--card-dark-edge) 100%);
    box-shadow: 0 10px 24px rgba(0,0,0,.45);
  }
  .card--back { top: 100px; }
  .card--front { top: 476px; }

  .brand {
    display: flex;
    align-items: center;
    gap: 14px;
  }
  .brand__dot {
    border-radius: 50%;
    background: var(--accent-red);
    flex: none;
  }
  .brand__name {
    font-weight: 900;
    color: var(--paper-white);
    letter-spacing: .06em;
    white-space: nowrap;
  }
  .card--back .brand {
    position: absolute;
    left: 50%; top: 50%;
    transform: translate(-50%, -50%);
  }
  .card--back .brand__dot { width: 64px; height: 64px; }
  .card--back .brand__name { font-size: 30px; }

  .front__panel {
    position: absolute;
    left: 0; top: 0;
    width: 560px; height: 320px;
  }
  .front__content {
    position: absolute;
    left: 30px; top: 30px;
    width: 270px;
  }
  .card--front .brand { gap: 12px; }
  .card--front .brand__dot { width: 36px; height: 36px; }
  .card--front .brand__name { font-size: 16px; }
  .person { margin-top: 22px; }
  .person__name {
    color: var(--accent-red);
    font-weight: 700;
    font-size: 21px;
    text-transform: uppercase;
    letter-spacing: .03em;
  }
  .person__role {
    color: var(--text-light);
    font-size: 13px;
    margin-top: 3px;
  }
  .address {
    margin-top: 14px;
    color: var(--text-muted);
    font-size: 12.5px;
    line-height: 1.45;
    font-style: normal;
  }
  .contacts {
    list-style: none;
    margin-top: 12px;
    color: var(--text-muted);
    font-size: 12.5px;
    line-height: 1.6;
  }
  .contacts li { display: flex; align-items: center; gap: 8px; white-space: nowrap; }
  .contacts svg { width: 11px; height: 11px; flex: none; }
</style>
</head>
<body>

<section class="card card--back" aria-label="Card back">
  <div class="brand">
    <span class="brand__dot"></span>
    <span class="brand__name">O VITALIS SYSTEMS</span>
  </div>
</section>

<section class="card card--front" aria-label="Card front">
  <svg class="front__panel" viewBox="0 0 560 320" aria-hidden="true">
    <circle cx="525" cy="55" r="210" fill="var(--paper-white)"/>
  </svg>

  <div class="front__content">
    <div class="brand">
      <span class="brand__dot"></span>
      <span class="brand__name">O VITALIS SYSTEMS</span>
    </div>

    <div class="person">
      <p class="person__name">Odile Brevard</p>
      <p class="person__role">Chef de Projet</p>
    </div>

    <address class="address">
      318 Gaston Lemaire Street<br>
      59710 BÉTHUNE
    </address>

    <ul class="contacts">
      <li>
        <svg viewBox="0 0 12 12"><path d="M2.5 1h2l1 2.5-1.3 1a6 6 0 0 0 3.3 3.3l1-1.3L11 7.5v2a1.5 1.5 0 0 1-1.5 1.5A8.5 8.5 0 0 1 1 2.5 1.5 1.5 0 0 1 2.5 1z" fill="var(--accent-red)"/></svg>
        +33 (0) 327 481 605
      </li>
      <li>
        <svg viewBox="0 0 12 12"><rect x="3" y="0.5" width="6" height="11" rx="1.2" fill="none" stroke="var(--accent-red)" stroke-width="1.4"/><circle cx="6" cy="9.3" r=".8" fill="var(--accent-red)"/></svg>
        06 42 19 37 64
      </li>
      <li>
        <svg viewBox="0 0 12 12"><circle cx="6" cy="6" r="5" fill="none" stroke="var(--accent-red)" stroke-width="1.3"/><path d="M1 6h10M6 1c-2.4 3-2.4 7 0 10M6 1c2.4 3 2.4 7 0 10" fill="none" stroke="var(--accent-red)" stroke-width="1"/></svg>
        www.quorvexsystems.example
      </li>
      <li>
        <svg viewBox="0 0 12 12"><rect x="0.7" y="2.2" width="10.6" height="7.6" rx="1" fill="none" stroke="var(--accent-red)" stroke-width="1.3"/><path d="M1 2.8l5 3.8 5-3.8" fill="none" stroke="var(--accent-red)" stroke-width="1.2"/></svg>
        o.brevard@o-vitalissystems.example
      </li>
    </ul>
  </div>
</section>

</body>
</html>
```